Whitcombe Business Card Design

The name of the business is Dario Whitcombe, CPA LLC
The service that we offer is Accounting, Tax & Consulting Services. I need it to have the following items:
Dario Whitcombe, Principal
Phone Number
Email Address
Physical Address

I have attached the company logo, one in black and one in white. Please provide a design in black background and the other in white background. Please include "Accounting, Tax & Consulting Services". I want the business card to be clean and very professional.

```html
<!DOCTYPE html>
<html lang="en">
<head>
<meta charset="UTF-8">
<title>Dario Whitcombe, CPA LLC – Business Cards</title>
<link rel="stylesheet" href="https://fonts.googleapis.com/css2?family=Montserrat:wght@400;500;600;700&display=swap">
<style>
  :root {
    --backdrop: #dcdddc;
    --card-dark: #000000;
    --card-light: #ffffff;
    --ink-light: #f2f2f2;
    --ink-dark: #2b2b2d;
    --ink-muted: #8c8c8c;
    --accent: #a31a1d;
    --rule: #2b2b2d;
    --card-shadow: 0 2px 6px rgba(0,0,0,0.25);
  }
  * { margin: 0; padding: 0; box-sizing: border-box; }
  html, body {
    width: 1200px; height: 800px; overflow: hidden;
    background: var(--backdrop);
    font-family: "Montserrat", sans-serif;
  }
  .canvas { position: relative; width: 1200px; height: 800px; }

  .card { position: absolute; box-shadow: var(--card-shadow); }

  /* Front: black card */
  .card--front {
    left: 193px; top: 102px; width: 431px; height: 269px;
    background: var(--card-dark); color: var(--ink-light);
  }
  .front__brand {
    position: absolute; left: 66px; top: 48px;
    display: flex; align-items: center; gap: 7px;
  }
  .front__brand-mark { width: 14px; height: 14px; background: var(--accent); }
  .front__brand-name {
    font-size: 8px; font-weight: 500; letter-spacing: 1px;
    text-transform: uppercase; color: var(--ink-light);
  }
  .front__name {
    position: absolute; left: 63px; top: 120px; width: 140px;
    font-size: 18px; font-weight: 500; line-height: 24px;
    letter-spacing: 1.6px; text-transform: uppercase; white-space: nowrap;
  }
  .front__title {
    position: absolute; left: 62px; top: 178px; width: 133px; height: 18px;
    background: var(--card-light); color: var(--card-dark);
    font-size: 11.5px; font-weight: 500; letter-spacing: 1.3px;
    line-height: 18px; padding-left: 5px;
  }
  .front__divider {
    position: absolute; left: 215px; top: 116px; width: 1px; height: 89px;
    background: var(--ink-light);
  }
  .front__contacts { position: absolute; left: 236px; top: 128px; list-style: none; }
  .contact {
    display: flex; align-items: center; gap: 7px;
    height: 18px; margin-bottom: 5.5px;
    font-size: 8.5px; font-weight: 400; letter-spacing: 0.2px;
  }
  .contact__icon { width: 9px; height: 9px; fill: var(--ink-light); flex: none; }

  /* Back: white card */
  .card--back {
    left: 567px; top: 424px; width: 441px; height: 275px;
    background: var(--card-light); color: var(--ink-dark);
  }
  .back__mark {
    position: absolute; left: 71px; top: 106px; width: 35px; height: 35px;
    background: var(--accent);
  }
  .back__firm {
    position: absolute; left: 120px; top: 104px;
    font-size: 15.5px; font-weight: 600; letter-spacing: 0.3px;
    text-transform: uppercase; color: var(--ink-dark); white-space: nowrap;
  }
  .back__designation {
    position: absolute; left: 122px; top: 125px;
    font-size: 10.6px; font-weight: 600; letter-spacing: 1.7px;
    text-transform: uppercase; color: var(--ink-muted); white-space: nowrap;
  }
  .back__rule {
    position: absolute; left: 67px; top: 150px; width: 304px; height: 1px;
    background: var(--rule);
  }
  .back__services {
    position: absolute; left: 67px; top: 154px; width: 304px; text-align: center;
    font-size: 11.4px; font-weight: 500; letter-spacing: 0.5px; color: var(--ink-dark);
  }
</style>
</head>
<body>
<main class="canvas">

  <section class="card card--front">
    <div class="front__brand">
      <span class="front__brand-mark"></span>
      <span class="front__brand-name">Dario Whitcombe, CPA LLC</span>
    </div>
    <h1 class="front__name">Dario<br>Whitcombe</h1>
    <p class="front__title">PRINCIPAL</p>
    <div class="front__divider"></div>
    <ul class="front__contacts">
      <li class="contact">
        <svg class="contact__icon" viewBox="0 0 24 24"><path d="M6.6 10.8c1.4 2.8 3.8 5.1 6.6 6.6l2.2-2.2c.3-.3.7-.4 1-.2 1.1.4 2.3.6 3.6.6.6 0 1 .4 1 1V20c0 .6-.4 1-1 1C10.6 21 3 13.4 3 4c0-.6.4-1 1-1h3.5c.6 0 1 .4 1 1 0 1.3.2 2.5.6 3.6.1.3 0 .7-.2 1L6.6 10.8z"/></svg>
        <span>+12 345 678 90</span>
      </li>
      <li class="contact">
        <svg class="contact__icon" viewBox="0 0 24 24"><path d="M2 5h20v14H2V5zm2 2v.5l8 5 8-5V7l-8 5-8-5z"/></svg>
        <span>email@yourcompany.com</span>
      </li>
      <li class="contact">
        <svg class="contact__icon" viewBox="0 0 24 24"><path d="M12 2C8.1 2 5 5.1 5 9c0 5.2 7 13 7 13s7-7.8 7-13c0-3.9-3.1-7-7-7zm0 9.5A2.5 2.5 0 1 1 12 6.5a2.5 2.5 0 0 1 0 5z"/></svg>
        <span>Company address line</span>
      </li>
    </ul>
  </section>

  <section class="card card--back">
    <span class="back__mark"></span>
    <p class="back__firm">Dario Whitcombe, CPA, LLC</p>
    <p class="back__designation">Certified Public Accountant</p>
    <div class="back__rule"></div>
    <p class="back__services">Accounting, Tax &amp; Consulting Services</p>
  </section>

</main>
</body>
</html>
```